need corporate, modern business card created for Consulting Company

I need a slick business card using elements from my website, as well as, integrating my pixelforge-created logo (see files).

The business card needs to be:
1. Corporate and modern
2. Clean and professional

I've included a PSD with the logo/icon that you can use to create it. Feel free to try a metallic finish on the logo, make it bigger/small, underlay it. Whatever you need to do to make my card stand out.

Try a black background, or white background or gray.

The idea is for my card to be memorable as well as professional and corporate.

Target Market(s)

Corporate business in the US and Canada.

Industry/Entity Type

Business

Contact Information for Business Card

Commerce Advancing Methods
Martin Coles, Senior Partner
office: 1 877 555 0143
mobile: 1 519 555 0172
website: http://www.brightvale.example

Requirements
Must have
• Card-related information
• corporate, yet modern
• clean and professional
• incorporate the icon only
• must have an editable form when complete!
Nice to have
• metallic icon might be cool
• try it with white or black

```html
<!DOCTYPE html>
<html lang="en">
<head>
<meta charset="utf-8">
<title>Brightvale Business Card</title>
<link href="https://fonts.googleapis.com/css2?family=Michroma&display=swap" rel="stylesheet">
<style>
  :root {
    --page-bg: #e9e9e9;
    --card-black: #252525;
    --band-black: #161616;
    --band-grey: #a9abae;
    --brand-blue: #2f6cc0;
    --text-white: #f2f2f2;
    --divider: #bdbdbd;
  }
  html, body {
    margin: 0;
    padding: 0;
    width: 1200px;
    height: 901px;
    overflow: hidden;
    background: var(--page-bg);
  }
  .card {
    position: absolute;
    left: 150px;
    top: 193px;
    width: 900px;
    height: 514px;
    border-radius: 44px;
    background: var(--card-black);
    overflow: hidden;
    font-family: "Michroma", sans-serif;
    color: var(--text-white);
    box-shadow: 0 12px 30px rgba(0,0,0,0.25);
  }
  .card-swoosh {
    position: absolute;
    inset: 0;
    width: 900px;
    height: 514px;
  }
  .brand {
    position: absolute;
    top: 96px;
    left: 0;
    width: 900px;
    display: flex;
    justify-content: center;
    align-items: center;
    gap: 16px;
  }
  .brand-mark {
    width: 40px;
    height: 40px;
    background: var(--brand-blue);
  }
  .brand-name {
    font-size: 50px;
    color: var(--brand-blue);
    letter-spacing: -1px;
    line-height: 1;
  }
  .holder {
    position: absolute;
    top: 205px;
    right: 505px;
    text-align: right;
    text-transform: uppercase;
    white-space: nowrap;
  }
  .holder-name { font-size: 16px; letter-spacing: 2px; margin: 0 0 6px; line-height: 22px; }
  .holder-title { font-size: 12px; letter-spacing: 2px; margin: 0 0 18px; line-height: 18px; }
  .holder-address { font-size: 13px; letter-spacing: 1px; line-height: 24px; margin: 0; }
  .divider {
    position: absolute;
    left: 412px;
    top: 203px;
    width: 1px;
    height: 132px;
    background: var(--divider);
  }
  .contacts {
    position: absolute;
    top: 205px;
    left: 428px;
    margin: 0;
    padding: 0;
    list-style: none;
    white-space: nowrap;
  }
  .contacts li {
    display: flex;
    align-items: center;
    gap: 9px;
    height: 25px;
    font-size: 14px;
    letter-spacing: 1.5px;
  }
  .contact-icon { width: 15px; height: 15px; flex: none; }
</style>
</head>
<body>
  <div class="card">
    <svg class="card-swoosh" viewBox="0 0 900 514" aria-hidden="true">
      <path d="M0,260 C120,330 420,400 900,470 L900,514 L0,514 Z" fill="var(--band-grey)"/>
      <path d="M0,280 C120,350 420,414 900,480 L900,514 L0,514 Z" fill="var(--band-black)"/>
      <path d="M0,316 C120,380 420,432 900,490 L900,514 L0,514 Z" fill="var(--brand-blue)"/>
    </svg>

    <div class="brand">
      <span class="brand-mark"></span>
      <span class="brand-name">brightvale</span>
    </div>

    <div class="holder">
      <p class="holder-name">Martin Coles</p>
      <p class="holder-title">Senior Partner</p>
      <p class="holder-address">Suite # 410, Vale Bldg,<br>ON 55210</p>
    </div>

    <div class="divider"></div>

    <ul class="contacts">
      <li>
        <svg class="contact-icon" viewBox="0 0 16 16"><circle cx="8" cy="8" r="8" fill="#fff"/><path d="M5 4 L7 4 L7.5 6 L6.5 7 Q7.5 9 9 9.5 L10 8.5 L12 9 L12 11 Q7 11.5 5 4 Z" fill="var(--card-black)"/></svg>
        1 877 555 0143
      </li>
      <li>
        <svg class="contact-icon" viewBox="0 0 16 16"><circle cx="8" cy="8" r="8" fill="#fff"/><rect x="5.5" y="3" width="5" height="10" rx="1" fill="var(--card-black)"/><rect x="6.5" y="4.5" width="3" height="5.5" fill="#fff"/></svg>
        1 519 555 0172
      </li>
      <li>
        <svg class="contact-icon" viewBox="0 0 16 16"><circle cx="8" cy="8" r="8" fill="#fff"/><rect x="4" y="6" width="8" height="6" fill="var(--card-black)"/><rect x="5.5" y="3.5" width="5" height="3" fill="var(--card-black)"/><rect x="5.5" y="8" width="5" height="1" fill="#fff"/></svg>
        1 877 555 0199
      </li>
      <li>
        <svg class="contact-icon" viewBox="0 0 16 16"><circle cx="8" cy="8" r="8" fill="#fff"/><rect x="3.5" y="5" width="9" height="6" fill="var(--card-black)"/><path d="M3.5 5 L8 8.5 L12.5 5" stroke="#fff" stroke-width="1" fill="none"/></svg>
        name@brightvale.example
      </li>
      <li>
        <svg class="contact-icon" viewBox="0 0 16 16"><circle cx="8" cy="8" r="8" fill="#fff"/><circle cx="8" cy="8" r="4.5" fill="none" stroke="var(--card-black)" stroke-width="1.2"/><path d="M3.5 8 H12.5 M8 3.5 V12.5" stroke="var(--card-black)" stroke-width="1"/></svg>
        www.brightvale.example
      </li>
    </ul>
  </div>
</body>
</html>
```